Business Card - Business Consultancy

Newly Established Company, specializing in Business Consultancy, Human Resource Management, Talent Acquisition and Payroll Solutions.

We need a Business card design which portrays "elegance" and a very sleek yet business-like design. We would like a nice blue trimming (which goes well with the logo) to separate the content of the business card at the top. We would also like to see the design using the color silver either as a background or incorporated into it.

The final design should be a Business card which has colors matching the logo; a nice font; the above-mentioned specifics that adheres to the theme of "a stylish and professional business"

FYI: please do not have too fanciful designs.

Industry/Entity Type

Business Consultant

Contact Information for Business Card

Darren Lim
Business Development Director
Arbor Talent Consulting Private Limited
27 Wexley Street, #05-03B
Harbourgate Trade Building
Singapore 059317
Mobile : (+65) 98354417
Email : dlim@arbortalent-advisory.com
Alternative : arbortalentadvisory@mailbox-example.com

Requirements
Must have
• Nice Blue Trimming matching Logo which separates content, see attached
• Design incorporates either a silver background or the use of the color silver
Should not have
• No Fanciful Designs
• No Childish Designs
• No Overly Complicated Designs

```html
<!DOCTYPE html>
<html lang="en">
<head>
<meta charset="utf-8">
<title>Arbor Talent Consulting – Business Cards</title>
<link rel="stylesheet" href="https://fonts.googleapis.com/css2?family=Open+Sans:wght@400;600;700&display=swap">
<style>
  :root {
    --page-bg: #e6e7e9;
    --card-white: #ffffff;
    --silver: #eceef0;
    --brand-blue: #1f7fd6;
    --trim-green: #7cbf2a;
    --ink: #2a2d31;
    --text-light: #ffffff;
    --shadow: rgba(0, 0, 0, 0.18);
  }
  * { box-sizing: border-box; margin: 0; padding: 0; }
  html, body {
    width: 1200px;
    height: 900px;
    overflow: hidden;
    background: var(--page-bg);
    font-family: "Open Sans", Arial, sans-serif;
  }
  .canvas {
    position: relative;
    width: 1200px;
    height: 900px;
  }
  .card {
    position: absolute;
    width: 600px;
    height: 343px;
    background: linear-gradient(180deg, var(--card-white) 0%, var(--silver) 100%);
    box-shadow: 0 10px 28px var(--shadow);
    overflow: hidden;
  }
  .card--front { left: 80px; top: 90px; }
  .card--back { left: 520px; top: 467px; }

  .card__top {
    position: absolute;
    left: 0; right: 0; top: 0;
    display: flex;
    align-items: center;
    justify-content: center;
  }
  .card--front .card__top { height: 196px; }
  .card--back .card__top { height: 146px; }

  .card__trim {
    position: absolute;
    left: 0; right: 0;
    height: 6px;
    background: var(--trim-green);
  }
  .card--front .card__trim { top: 196px; }
  .card--back .card__trim { top: 146px; }

  .card__band {
    position: absolute;
    left: 0; right: 0; bottom: 0;
    background: var(--brand-blue);
    color: var(--text-light);
  }
  .card--front .card__band { top: 202px; }
  .card--back .card__band { top: 152px; }

  .brand {
    display: flex;
    align-items: center;
    gap: 16px;
  }
  .brand__dot {
    width: 62px;
    height: 62px;
    border-radius: 50%;
    background: var(--brand-blue);
  }
  .brand__name {
    font-weight: 700;
    font-size: 30px;
    line-height: 1.05;
    color: var(--ink);
    letter-spacing: 0.5px;
  }

  .tagline {
    position: absolute;
    left: 0; right: 0; top: 30px;
    text-align: center;
    font-weight: 700;
    font-size: 19px;
    line-height: 1.35;
    padding: 0 90px;
  }

  .contact-person {
    position: absolute;
    left: 40px;
    top: 14px;
  }
  .contact-person__name {
    font-weight: 700;
    font-size: 20px;
    line-height: 1.2;
  }
  .contact-person__role {
    font-size: 14px;
    line-height: 1.3;
  }
  .contact-person__company {
    margin-top: 16px;
    font-weight: 700;
    font-size: 14px;
  }
  .contact-person__address {
    margin-top: 6px;
    font-size: 15px;
    line-height: 1.55;
  }

  .contact-lines {
    position: absolute;
    right: 24px;
    top: 16px;
    list-style: none;
    text-align: right;
    font-size: 11.5px;
    line-height: 1.9;
  }
  .contact-lines li {
    display: flex;
    align-items: center;
    justify-content: flex-end;
    gap: 6px;
  }
  .contact-lines svg { width: 11px; height: 11px; flex: none; }
</style>
</head>
<body>
<main class="canvas">

  <section class="card card--front" aria-label="Business card front">
    <div class="card__top">
      <div class="brand">
        <span class="brand__dot" aria-hidden="true"></span>
        <span class="brand__name">Arbor Talent<br>Consulting</span>
      </div>
    </div>
    <div class="card__trim"></div>
    <div class="card__band">
      <p class="tagline">Recruitment | HR Solutions | Business Consultancy</p>
    </div>
  </section>

  <section class="card card--back" aria-label="Business card back">
    <div class="card__top">
      <div class="brand">
        <span class="brand__dot" aria-hidden="true"></span>
        <span class="brand__name">Arbor Talent<br>Consulting</span>
      </div>
    </div>
    <div class="card__trim"></div>
    <div class="card__band">
      <div class="contact-person">
        <p class="contact-person__name">Darren Lim</p>
        <p class="contact-person__role">Business Development Director</p>
        <p class="contact-person__company">Arbor Talent Consulting Private Limited</p>
        <p class="contact-person__address">27 Wexley Street, #05-03B<br>Harbourgate Trade Building<br>Singapore 059317</p>
      </div>
      <ul class="contact-lines">
        <li>(+65) 98354417
          <svg viewBox="0 0 12 12" aria-hidden="true"><path fill="#fff" d="M2.4 1l2 2-1 1.3a7 7 0 0 0 4.3 4.3L9 7.6l2 2L9.6 11C5 10.6 1.4 7 1 2.4z"/></svg>
        </li>
        <li>dlim@arbortalent-advisory.com
          <svg viewBox="0 0 12 12" aria-hidden="true"><rect x="1" y="2.5" width="10" height="7" fill="#fff"/><path d="M1 2.5l5 4 5-4" fill="none" stroke="#1f7fd6" stroke-width="1"/></svg>
        </li>
        <li>arbortalentadvisory@mailbox-example.com
          <svg viewBox="0 0 12 12" aria-hidden="true"><rect x="1" y="2.5" width="10" height="7" fill="#fff"/><path d="M1 2.5l5 4 5-4" fill="none" stroke="#1f7fd6" stroke-width="1"/></svg>
        </li>
      </ul>
    </div>
  </section>

</main>
</body>
</html>
```